Stylish new business card needed!

Hello everyone! I am in need of a new business card design for an alarm company here in Hurricane WV. I have all fonts, color codes and logos provided for you use! We are a young company and like the style of a clean sleek looking business card. Would like it double sided, one side holding the logo and the other with your design!
Target Market(s)
The people that are looking for the newest tech for home automation and security
Industry/Entity Type
Alarm services; Home automation
Contact Information for Business Card
Name of person; position (Sales; Installer); Phone Number (555.418.7260); Employee cell Number; Website (www.GuardedByVelk.example); Employee Email; Double sided
Look and feel
Each slider illustrates characteristics of the customer's brand and the style your logo design should communicate.

```html
<!DOCTYPE html>
<html lang="en">
<head>
<meta charset="utf-8">
<title>Guarded By Velk – Business Card</title>
<link rel="stylesheet" href="https://fonts.googleapis.com/css2?family=Arimo:wght@400;700&display=swap">
<style>
  :root {
    --backdrop: #2b2b2e;
    --card-light: #ffffff;
    --card-dark: #212124;
    --brand-orange: #f08a4b;
    --brand-grey: #8f8f8f;
    --ink: #111111;
  }
  * { box-sizing: border-box; margin: 0; padding: 0; }
  html, body {
    width: 1200px; height: 780px; overflow: hidden;
    background: var(--backdrop);
    font-family: "Arimo", Arial, sans-serif;
  }
  .canvas {
    width: 1200px; height: 780px;
    display: flex; align-items: center; justify-content: center; gap: 40px;
  }
  .card {
    width: 540px; height: 309px;
    border-radius: 22px;
    position: relative; overflow: hidden;
    box-shadow: 0 14px 30px rgba(0,0,0,.35);
  }

  /* Front: contact side */
  .card--front { background: var(--card-light); display: flex; }
  .front__brand {
    width: 47%; padding: 34px 0 0 34px;
  }
  .wordmark {
    font-weight: 700; color: var(--brand-orange);
    text-transform: uppercase; line-height: 1;
    display: flex; align-items: center; gap: 8px;
  }
  .wordmark__dot {
    width: 12px; height: 12px; border-radius: 50%;
    background: var(--brand-orange); flex: none;
  }
  .front__brand .wordmark { font-size: 21px; }
  .tagline {
    font-weight: 700; color: var(--brand-orange);
    text-transform: uppercase; letter-spacing: .02em;
  }
  .front__brand .tagline { font-size: 8px; margin-top: 10px; }

  .front__divider {
    width: 1px; background: var(--ink);
    margin: 110px 0 30px;
  }
  .front__details { flex: 1; padding: 120px 20px 0 26px; }
  .person__name { font-size: 27px; font-weight: 700; line-height: 1; }
  .person__first { color: var(--brand-orange); }
  .person__last { color: var(--brand-grey); }
  .person__role { font-size: 13px; font-weight: 700; color: var(--ink); margin-top: 6px; }
  .contact { list-style: none; margin-top: 14px; }
  .contact__item {
    display: flex; align-items: center; gap: 8px;
    font-size: 13px; color: var(--ink); line-height: 19px;
  }
  .contact__icon { width: 11px; height: 11px; flex: none; }

  /* Back: brand side */
  .card--back {
    background: var(--card-dark);
    display: flex; flex-direction: column; align-items: center; justify-content: center;
  }
  .card--back .wordmark { font-size: 40px; gap: 14px; }
  .card--back .wordmark__dot { width: 22px; height: 22px; }
  .card--back .tagline { font-size: 12px; margin-top: 18px; }
</style>
</head>
<body>
<main class="canvas">
  <section class="card card--front" aria-label="Business card, contact side">
    <div class="front__brand">
      <div class="wordmark"><span class="wordmark__dot"></span>Guarded by Velk</div>
      <p class="tagline">Automation and Security Services</p>
    </div>
    <div class="front__divider"></div>
    <div class="front__details">
      <h1 class="person__name"><span class="person__first">Mira</span> <span class="person__last">Holden</span></h1>
      <p class="person__role">Sales; Installer</p>
      <ul class="contact">
        <li class="contact__item">
          <svg class="contact__icon" viewBox="0 0 12 12" aria-hidden="true"><path d="M2.5 1l2 2.2-1 1.3a7 7 0 0 0 4 4l1.3-1 2.2 2-1.3 1.5C5 11 1 7 1 2.3z" fill="var(--brand-orange)"/></svg>
          555.418.7260
        </li>
        <li class="contact__item">
          <svg class="contact__icon" viewBox="0 0 12 12" aria-hidden="true"><rect x="3" y="0.7" width="6" height="10.6" rx="1" fill="none" stroke="var(--brand-orange)" stroke-width="1.2"/><circle cx="6" cy="9.3" r=".7" fill="var(--brand-orange)"/></svg>
          555.302.8814
        </li>
        <li class="contact__item">
          <svg class="contact__icon" viewBox="0 0 12 12" aria-hidden="true"><circle cx="6" cy="6" r="5" fill="none" stroke="var(--brand-orange)" stroke-width="1.2"/><path d="M1 6h10M6 1c-2.5 2.8-2.5 7.2 0 10M6 1c2.5 2.8 2.5 7.2 0 10" fill="none" stroke="var(--brand-orange)" stroke-width="1"/></svg>
          www.GuardedByVelk.example
        </li>
        <li class="contact__item">
          <svg class="contact__icon" viewBox="0 0 12 12" aria-hidden="true"><rect x="0.7" y="2.2" width="10.6" height="7.6" rx="1" fill="none" stroke="var(--brand-orange)" stroke-width="1.2"/><path d="M1 3l5 4 5-4" fill="none" stroke="var(--brand-orange)" stroke-width="1.2"/></svg>
          info@GuardedByVelk.example
        </li>
      </ul>
    </div>
  </section>

  <section class="card card--back" aria-label="Business card, brand side">
    <div class="wordmark"><span class="wordmark__dot"></span>Guarded by Velk</div>
    <p class="tagline">Automation and Security Services</p>
  </section>
</main>
</body>
</html>
```